Corvana Tongue Works, LLC

We need a business card that includes information about our business and conveys a reliable business that provides document translation services and interpreters for a variety of corporate and individual clients. We want to come across as professional, reliable, yet approachable. It should include the following on one side:

ESL / ENL Language Classes, Private Lessons, and Online Tutors
PLEXA Training and Testing
Translating & Interpreting Services
Contact us about Over-the-Phone Interpreting in over 200 languages
24/7/365
www.corvanatongue.example

The other side should include (555) 481-3062

Rhoda Pelling, President
482 Garnet Ave., Ste. 219
Indianapolis, IN 40917

Please add USA as part of the address. Also, please add rmpelling@corvanatongueworks.example as the e-mail address. Thank you.

Target Market(s)

Business professionals, their families, the international community

Industry/Entity Type

Business

Contact Information for Business Card

24/7/365
www.corvanatongue.example

(555) 481-3062

Rhoda Pelling, President
482 Garnet Ave., Ste. 219
Indianapolis, IN 40917
USA

Font styles to use
Sans Serif

Colors

Designer to choose colors to be used in the design.

Requirements
Must have
• See project description
• e-mail address and web address
• Phone number
Nice to have
• a globe
• physical address
Should not have
• Should not have the same color scheme as other agencies in our market in Indiana unless it is blue and black. No purple or yellow.

```html
<!DOCTYPE html>
<html lang="en">
<head>
<meta charset="utf-8">
<title>Corvana Tongue Works, LLC — Business Card</title>
<link href="https://fonts.googleapis.com/css2?family=Open+Sans:wght@400;600;700&display=swap" rel="stylesheet">
<style>
  :root {
    --bg: #e4e4e4;
    --charcoal: #2e3136;
    --charcoal-light: #3a3e44;
    --brand-blue: #1795d0;
    --ink: #222427;
    --white: #ffffff;
  }
  * { box-sizing: border-box; margin: 0; padding: 0; }
  html, body {
    width: 1200px; height: 852px; overflow: hidden;
    background: var(--bg);
    font-family: "Open Sans", Arial, sans-serif;
  }
  .stage { position: relative; width: 1200px; height: 852px; }
  .card {
    position: absolute; width: 600px; height: 343px;
    border-radius: 26px; overflow: hidden;
    box-shadow: 0 6px 18px rgba(0,0,0,.18);
  }

  /* Back side */
  .card-back { left: 90px; top: 60px; background: var(--charcoal); color: var(--white); }
  .world-area {
    position: absolute; left: 40px; top: 30px; width: 520px; height: 250px;
    border-radius: 40%;
    background: radial-gradient(ellipse at center, var(--charcoal-light) 0%, rgba(58,62,68,.5) 55%, rgba(46,49,54,0) 75%);
  }
  .services {
    position: absolute; left: 0; right: 0; top: 48px;
    text-align: center; font-size: 17px; line-height: 25px; list-style: none;
  }
  .services .chev { color: var(--brand-blue); margin-right: 6px; font-weight: 700; }
  .services .sep { display: inline-block; width: 18px; }
  .divider {
    position: absolute; left: 160px; width: 280px; top: 160px;
    height: 2px; background: var(--brand-blue);
  }
  .otp {
    position: absolute; left: 0; right: 0; top: 172px;
    text-align: center; font-size: 17px; line-height: 25px;
  }
  .back-web {
    position: absolute; left: 0; right: 0; bottom: 28px;
    text-align: center; font-size: 16px;
  }
  .back-web .domain { color: var(--brand-blue); }

  /* Front side */
  .card-front { left: 510px; top: 440px; background: var(--white); }
  .front-shape { position: absolute; inset: 0; }
  .brand {
    position: absolute; left: 300px; top: 52px;
    display: flex; align-items: center; gap: 14px;
  }
  .brand-dot {
    width: 74px; height: 74px; border-radius: 50%;
    background: var(--brand-blue); border: 4px solid var(--white);
    box-shadow: 0 0 0 3px var(--brand-blue);
    flex: none;
  }
  .brand-name {
    font-size: 24px; line-height: 28px; font-weight: 600; color: var(--ink);
    width: 200px;
  }
  .tagline {
    position: absolute; right: 0; top: 196px; width: 270px; height: 24px;
    background: var(--ink); color: var(--white);
    font-size: 11px; line-height: 24px; text-align: center;
    white-space: nowrap;
  }
  .person { position: absolute; left: 34px; top: 70px; color: var(--white); }
  .person-name { font-size: 23px; font-weight: 700; }
  .person-title { font-size: 13px; margin-left: 18px; margin-top: 2px; }
  .contact {
    position: absolute; left: 34px; top: 196px; color: var(--white);
    font-size: 13.5px; line-height: 21px; list-style: none;
  }
  .contact li { display: flex; align-items: center; gap: 8px; white-space: nowrap; }
  .contact svg { width: 14px; height: 14px; flex: none; }
</style>
</head>
<body>
<main class="stage">

  <section class="card card-back" aria-label="Card back: services">
    <div class="world-area" role="img" aria-label="Faint world map in the background"></div>
    <ul class="services">
      <li><span class="chev">»</span>ESL / ENL Language Classes</li>
      <li><span class="chev">»</span>Private Lessons<span class="sep"></span><span class="chev">»</span>Online Tutors</li>
      <li><span class="chev">»</span>PLEXA Training and Testing</li>
      <li><span class="chev">»</span>Translating &amp; Interpreting Services</li>
    </ul>
    <div class="divider"></div>
    <p class="otp">Contact us about Over-the-Phone<br>Interpreting in over 200 languages<br>24/7/365</p>
    <p class="back-web">www.<span class="domain">corvanatongue</span>.example</p>
  </section>

  <section class="card card-front" aria-label="Card front: contact">
    <svg class="front-shape" viewBox="0 0 600 343" preserveAspectRatio="none" aria-hidden="true">
      <polygon points="0,0 205,0 500,343 0,343" fill="var(--brand-blue)"/>
    </svg>

    <div class="brand">
      <span class="brand-dot" aria-hidden="true"></span>
      <span class="brand-name">Corvana Tongue Works, LLC</span>
    </div>
    <div class="tagline">Interpreting | Translating | Language Training</div>

    <div class="person">
      <p class="person-name">Rhoda Pelling</p>
      <p class="person-title">President</p>
    </div>

    <ul class="contact">
      <li>482 Garnet Ave., Ste. 219</li>
      <li>Indianapolis, IN 40917 USA</li>
      <li>
        <svg viewBox="0 0 16 16" aria-hidden="true"><path fill="#fff" d="M3 2h3l1.2 3-1.7 1.2a8 8 0 0 0 4.3 4.3L11 8.8 14 10v3a1.5 1.5 0 0 1-1.6 1.5A12 12 0 0 1 1.5 3.6 1.5 1.5 0 0 1 3 2z"/></svg>
        (555) 481-3062
      </li>
      <li>
        <svg viewBox="0 0 16 16" aria-hidden="true"><rect x="1.5" y="3.5" width="13" height="9" fill="none" stroke="#fff" stroke-width="1.5"/><path d="M1.5 3.5 8 9l6.5-5.5" fill="none" stroke="#fff" stroke-width="1.5"/></svg>
        rmpelling@corvanatongueworks.example
      </li>
      <li>
        <svg viewBox="0 0 16 16" aria-hidden="true"><circle cx="8" cy="8" r="6.3" fill="none" stroke="#fff" stroke-width="1.4"/><ellipse cx="8" cy="8" rx="2.7" ry="6.3" fill="none" stroke="#fff" stroke-width="1.2"/><path d="M1.7 8h12.6" stroke="#fff" stroke-width="1.2"/></svg>
        www.corvanatongue.example
      </li>
    </ul>
  </section>

</main>
</body>
</html>
```